Certificates with Watermark Images

We are looking for a design of One page Certificates with Watermark (background) images where text will be printed over it .
Graphics design is required to reflect the flowing categories:
IPTV (Internet Protocol TV)
VoD (Video on Demand)
Satellite Receiver
Graphics design images for all three categories must be provided to maintain the same them .
Thank you and good luck.
Industry/Entity Type
Internet
Requirements
Must have
- Graphics design images for all three categories must be provided to maintain the same them

```html
<!DOCTYPE html>
<html lang="en">
<head>
<meta charset="utf-8">
<title>Certificate – Satellite Service</title>
<link rel="stylesheet" href="https://fonts.googleapis.com/css2?family=Fira+Sans:ital,wght@0,400;0,700;1,700&display=swap">
<style>
  :root {
    --page: #ffffff;
    --ink: #1d1d1f;
    --accent-blue: #1b98de;
    --brand-orange: #e8552a;
    --seal-blue: #2a14a8;
    --screen-glow: #ffffff;
    --screen-light: #eef2f6;
    --screen-mid: #d3dde6;
    --screen-deep: #9fb2c4;
    --screen-shade: #8ea3b8;
  }
  * { margin: 0; padding: 0; box-sizing: border-box; }
  html, body { width: 1200px; height: 845px; overflow: hidden; background: var(--page); }
  body { font-family: "Fira Sans", Arial, sans-serif; color: var(--ink); position: relative; }

  .certificate {
    position: absolute; left: 29px; top: 28px; width: 1145px; height: 790px;
    border-radius: 48px; overflow: hidden;
  }
  .certificate__backdrop {
    position: absolute; inset: 0;
    background:
      radial-gradient(ellipse 38% 45% at 28% 48%, rgba(250,251,253,0.95) 0%, rgba(250,251,253,0.7) 50%, rgba(250,251,253,0) 100%),
      radial-gradient(ellipse 14% 12% at 64% 22%, rgba(255,255,255,0.95) 0%, rgba(255,255,255,0) 100%),
      radial-gradient(ellipse 18% 16% at 80% 32%, rgba(255,255,255,0.85) 0%, rgba(255,255,255,0) 100%),
      radial-gradient(ellipse 16% 14% at 72% 58%, rgba(255,255,255,0.7) 0%, rgba(255,255,255,0) 100%),
      radial-gradient(ellipse 14% 12% at 92% 50%, rgba(255,255,255,0.7) 0%, rgba(255,255,255,0) 100%),
      radial-gradient(ellipse 30% 25% at 88% 85%, rgba(142,163,184,0.65) 0%, rgba(142,163,184,0) 100%),
      radial-gradient(ellipse 30% 22% at 15% 8%, rgba(159,178,196,0.45) 0%, rgba(159,178,196,0) 100%),
      radial-gradient(ellipse 22% 20% at 55% 88%, rgba(159,178,196,0.45) 0%, rgba(159,178,196,0) 100%),
      linear-gradient(100deg, var(--screen-light) 0%, var(--screen-mid) 40%, var(--screen-deep) 75%, var(--screen-mid) 100%);
  }

  .brand { position: absolute; left: 214px; top: 54px; width: 200px; text-align: center; }
  .brand__mark {
    display: block; width: 66px; height: 66px; margin: 0 auto 16px;
    border-radius: 50%; background: var(--brand-orange);
  }
  .brand__name { font-size: 24px; font-weight: 700; color: var(--ink); }

  .award { position: absolute; left: 16px; top: 218px; width: 600px; text-align: center; }
  .award__title { font-size: 44px; font-weight: 700; letter-spacing: 6px; line-height: 1; }
  .award__lead { font-size: 22px; margin-top: 20px; }
  .award__recipient { font-size: 42px; font-weight: 700; color: var(--accent-blue); margin-top: 4px; line-height: 1.1; }
  .award__category { font-size: 20px; margin-top: 16px; }
  .award__text { font-size: 19px; line-height: 27px; margin: 20px auto 0; width: 420px; }
  .award__value { font-size: 19px; font-weight: 700; margin-top: 14px; }

  .details {
    position: absolute; left: 76px; top: 634px;
    font-size: 12.5px; font-weight: 700; font-style: italic; line-height: 16px;
  }
  .details p + p { margin-top: 16px; }

  .signature {
    position: absolute; left: 276px; top: 642px; width: 84px; height: 80px;
    border-radius: 50%;
    background: radial-gradient(circle, rgba(58,47,176,0.25) 0%, rgba(58,47,176,0) 70%);
  }
  .seal { position: absolute; left: 464px; top: 614px; width: 134px; height: 134px; }
</style>
</head>
<body>
  <main class="certificate">
    <div class="certificate__backdrop" role="img" aria-label="Soft blue-grey wall of glowing video screens"></div>

    <header class="brand">
      <span class="brand__mark"></span>
      <span class="brand__name">Our Organization</span>
    </header>

    <section class="award">
      <h1 class="award__title">CERTIFICATE</h1>
      <p class="award__lead">this certificate that</p>
      <p class="award__recipient">Bright Horizon</p>
      <p class="award__category">(satellite service)</p>
      <p class="award__text">has been awarded for his labor achievements and many years of diligent work, also for his labor achievements and many years of diligent work.</p>
      <p class="award__value">and has passed for this Certificate $100</p>
    </section>

    <footer class="details">
      <p>Certificate No. 0000/1</p>
      <p>11 November 2011<br>New-York</p>
      <p>Our company Genera Director<br>Samir Valdane</p>
    </footer>

    <div class="signature" role="img" aria-label="Director's handwritten signature"></div>

    <svg class="seal" viewBox="0 0 134 134" aria-hidden="true">
      <polygon fill="var(--seal-blue)" points="67,2 73,13 83,4 86,16 98,10 98,22 111,19 108,31 121,31 115,42 127,45 119,55 130,61 120,68 130,75 119,80 127,90 115,93 121,104 108,104 111,116 98,113 98,125 86,119 83,131 73,122 67,132 61,122 51,131 48,119 36,125 36,113 23,116 26,104 13,104 19,93 7,90 15,80 4,75 14,68 4,61 15,55 7,45 19,42 13,31 26,31 23,19 36,22 36,10 48,16 51,4 61,13"/>
    </svg>
  </main>
</body>
</html>
```